Velmor Spire Nine Flash website

we need a website to cater to 2 aspect of the business. We have Velmor spire residence and velmor spire office. For the office, we will get their inquire and arrange a face to face meetup to show them the office area for rent. For the residence side, it will need to be like staylane or roomvio.com. we want to allow them to book online for the date they need. We have a total of 10 different room configurations starting at $70 per night and up depending on the size of the room. example of the design is https://brisquelodge.com/

Target Market(s)

the website should have detail information on the layout, designs, and luxury of the building.

Industry/Entity Type

office and service appartment rental/lease

Coding

Coded - Design and coding required

Number of Pages Required

5+ page

Requirements
Must have
• a luxury perspective
Nice to have
• example https://brisquelodge.com/

```html
<!DOCTYPE html>
<html lang="en">
<head>
<meta charset="utf-8">
<title>Velmor Spire Nine</title>
<link rel="stylesheet" href="https://fonts.googleapis.com/css2?family=Montserrat:wght@400;500;600&family=Roboto:wght@300;400&display=swap">
<style>
:root{
  --gold:#d9a033;
  --gold-dark:#b98526;
  --ink:#2b2b2b;
  --muted:#555;
  --dark:#222222;
  --footer:#7c4f2b;
  --panel:#f2f2f2;
  --white:#ffffff;
}
*{margin:0;padding:0;box-sizing:border-box}
html,body{width:1200px;height:4866px;overflow:hidden;background:var(--white)}
body{position:relative;font-family:"Roboto",sans-serif;font-weight:300;color:var(--muted)}
.abs{position:absolute}
h1,h2,h3,.display{font-family:"Montserrat",sans-serif;font-weight:500;color:var(--ink)}
.btn{position:absolute;display:flex;align-items:center;justify-content:center;font-family:"Roboto",sans-serif;font-weight:400;font-size:13px;border-radius:4px}
.btn-gold{background:var(--gold);color:var(--white)}
.btn-dark{background:#555;color:var(--white)}
.btn-outline{border:1.5px solid var(--gold);color:var(--ink);background:var(--white);justify-content:flex-start;padding-left:14px}
.photo{position:absolute}
.body-text{font-size:13.5px;line-height:17.5px;color:var(--muted)}
.rule{position:absolute;height:1px;background:var(--gold);width:170px}

/* header */
.logo{left:53px;top:28px;display:flex;flex-direction:column;align-items:center;gap:6px}
.logo-mark{width:30px;height:30px;background:var(--gold)}
.logo-name{font-family:"Montserrat",sans-serif;font-size:10px;color:var(--gold);letter-spacing:.3px}
.nav{top:43px;font-size:12.5px;color:var(--ink);font-weight:400}
.nav.active{color:var(--gold)}

/* hero */
.hero{left:0;top:102px;width:1196px;height:666px;background:radial-gradient(ellipse at 50% 40%,#c9a070 0%,#8a5e35 40%,#4a2f1a 80%,#2e1d10 100%)}
.hero-line{position:absolute;left:321px;width:556px;height:1px;background:rgba(255,255,255,.7)}
.hero h1{position:absolute;left:0;width:1196px;top:370px;text-align:center;color:var(--white);font-size:31px;font-weight:600}
.hero-sub{position:absolute;left:340px;width:516px;top:418px;text-align:center;color:#f2e6d8;font-size:13.5px;line-height:19px}

/* dark section */
.workspace{left:0;top:2585px;width:1196px;height:823px;background:var(--dark)}
.ws-title{left:53px;top:2645px;font-family:"Montserrat",sans-serif;font-weight:400;font-size:54px;color:var(--white)}
.ws-accent{left:53px;top:2722px;font-family:"Montserrat",sans-serif;font-weight:400;font-size:84px;color:var(--gold)}

/* about card */
.about{left:53px;top:3461px;width:1091px;height:498px;background:linear-gradient(135deg,#3a3d45 0%,#23252c 45%,#3d4049 70%,#55575e 100%)}
.about h2{position:absolute;left:0;width:100%;top:110px;text-align:center;color:var(--white);font-size:50px;font-weight:500}
.about-lead{position:absolute;left:50px;width:991px;top:198px;text-align:center;color:#e4e4e4;font-size:13.5px;line-height:18px}
.pillar{position:absolute;top:282px;width:300px;text-align:center}
.pillar h3{color:var(--white);font-size:29px;font-weight:500;margin-bottom:14px}
.pillar p{color:#dcdcdc;font-size:13.5px;line-height:17px}

/* contact */
.contact-panel{left:492px;top:4012px;width:704px;height:490px;background:var(--panel)}
.field{position:absolute;background:var(--white);border:1px solid #e2e2e2;border-radius:4px;font-size:11px;font-style:italic;color:#888;padding:8px 8px}

/* footer */
.footer{left:0;top:4559px;width:1196px;height:307px;background:var(--footer)}
.f-head{font-family:"Roboto",sans-serif;font-weight:400;font-size:13px;color:var(--white)}
.f-text{font-size:13px;color:#f1e6dc}
.social{width:33px;height:33px;border-radius:50%;background:var(--white)}
</style>
</head>
<body>

<!-- Header -->
<header>
  <div class="abs logo"><span class="logo-mark"></span><span class="logo-name">VELMOR SPIRE NINE</span></div>
  <nav>
    <span class="abs nav active" style="left:727px">Home</span>
    <span class="abs nav" style="left:790px">Residence</span>
    <span class="abs nav" style="left:879px">Office</span>
    <span class="abs nav" style="left:940px">About Us</span>
  </nav>
  <a class="btn btn-gold" style="left:1049px;top:34px;width:94px;height:34px">Contact Us</a>
</header>

<!-- Hero -->
<section class="abs hero" role="img" aria-label="Warm luxurious living room with chandelier, tufted sofa and tall windows">
  <div class="hero-line" style="top:253px"></div>
  <h1 style="top:268px">Unmatched Residential Experience</h1>
  <p class="hero-sub" style="top:316px">Experience luxury living and top-notch office spaces at Velmor Spire Nine. Offering a lavish lifestyle and a superior business environment.</p>
  <a class="btn btn-gold" style="left:566px;top:364px;width:81px;height:30px;font-size:12px">Learn More</a>
  <div class="hero-line" style="top:404px"></div>
</section>

<!-- Indulge -->
<section>
  <h2 class="abs" style="left:53px;top:822px;font-size:30px">Indulge in Luxury Living</h2>
  <div class="rule" style="left:53px;top:868px"></div>
  <p class="abs body-text" style="left:53px;top:880px;width:365px">Explore our luxurious residences at Velmor Spire Nine, where luxury meets comfort. Choose from a variety of meticulously designed rooms, each offering unparalleled elegance and sophistication. Whether you're looking for a cozy studio or a spacious penthouse, we have the perfect accommodation to suit your needs. Book now and experience the pinnacle of luxury living.</p>
  <div class="photo" style="left:445px;top:821px;width:751px;height:500px;background:linear-gradient(180deg,#3a3632 0%,#4c4640 45%,#b86d1d 70%,#5a4a3c 100%)" role="img" aria-label="Dark lounge with orange sectional sofa and large abstract painting"></div>
</section>

<!-- Room configurations -->
<section>
  <div class="photo" style="left:0;top:1427px;width:751px;height:500px;background:linear-gradient(180deg,#b9ab94 0%,#d8cbb6 45%,#a08a70 75%,#5b3a22 100%)" role="img" aria-label="Elegant bedroom with chandelier, large bed and wood floor"></div>
  <h2 class="abs" style="left:779px;top:1427px;font-size:30px">Room Configurations</h2>
  <div class="rule" style="left:779px;top:1474px"></div>
  <p class="abs body-text" style="left:779px;top:1484px;width:365px">Discover our range of room configurations tailored to meet your preferences. From cozy studios to expansive suites, each space is thoughtfully designed with your comfort in mind. Whether you're traveling solo or with family, we have the perfect accommodation option for you.</p>
  <a class="btn btn-gold" style="left:779px;top:1749px;width:74px;height:34px;justify-content:flex-start;padding-left:14px">Studio</a>
  <a class="btn btn-outline" style="left:779px;top:1797px;width:160px;height:34px">One-Bedroom Suite</a>
  <a class="btn btn-outline" style="left:779px;top:1844px;width:162px;height:34px">Two-Bedroom Suite</a>
  <a class="btn btn-outline" style="left:779px;top:1891px;width:172px;height:34px">Three-Bedroom Suite</a>
</section>

<!-- Book your stay -->
<section>
  <h2 class="abs" style="left:53px;top:2033px;font-size:30px">Book Your Stay</h2>
  <div class="rule" style="left:53px;top:2079px"></div>
  <p class="abs body-text" style="left:53px;top:2090px;width:360px">Ready to experience luxury living at Velmor Spire Nine? Book your stay now and secure your preferred room configuration for an unforgettable getaway. Our online staylane platform makes it easy to plan your stay from the comfort of your home. Reserve your room today and embark on a journey of luxury and indulgence.</p>
  <span class="abs display" style="left:53px;top:2221px;font-size:19px;font-weight:400;color:var(--gold)">Start From</span>
  <span class="abs display" style="left:53px;top:2248px;font-size:98px;font-weight:600;line-height:1;color:var(--gold-dark)">$70</span>
  <a class="btn btn-dark" style="left:53px;top:2402px;width:98px;height:34px">Book Now</a>
  <div class="photo" style="left:445px;top:2032px;width:751px;height:499px;background:linear-gradient(135deg,#c8a87f 0%,#e2c9a6 40%,#b88d5c 70%,#6e4226 100%)" role="img" aria-label="Bright hotel room with television, bed and warm walls"></div>
</section>

<!-- Workspace -->
<section class="abs workspace"></section>
<h2 class="abs ws-title">Discover Your Ideal</h2>
<span class="abs ws-accent">Workspace</span>
<p class="abs" style="left:611px;top:2638px;width:535px;font-size:13.5px;line-height:20.5px;color:#d8d8d8">Explore our premium office spaces at Velmor Spire Nine, where productivity meets luxury. From sleek private offices to collaborative coworking spaces, we offer a variety of workspace options tailored to meet your business needs. Each space is designed with cutting-edge technology and modern amenities to enhance your work environment. Find your ideal workspace and elevate your business to new heights.</p>
<a class="btn btn-gold" style="left:611px;top:2778px;width:110px;height:34px">Book a Tour</a>
<div class="photo" style="left:53px;top:2855px;width:166px;height:498px;background:linear-gradient(180deg,#f2f2f0 0%,#d9d4cc 60%,#b8895a 100%)" role="img" aria-label="White office with shelves and chairs"></div>
<div class="photo" style="left:251px;top:2855px;width:498px;height:498px;background:linear-gradient(180deg,#dcd6cc 0%,#c9b8a0 40%,#d07a3a 55%,#b8a78c 100%)" role="img" aria-label="Open lobby with orange lounge chairs and reception desk"></div>
<div class="photo" style="left:781px;top:2855px;width:166px;height:498px;background:linear-gradient(180deg,#2e5f9a 0%,#e8e4dc 35%,#e2c04a 70%,#2a4f7a 100%)" role="img" aria-label="Lounge with blue ceiling and yellow shelving"></div>
<div class="photo" style="left:979px;top:2855px;width:165px;height:498px;background:linear-gradient(180deg,#f0eee8 0%,#cfd6c2 50%,#b48a5c 100%)" role="img" aria-label="Bright cafe workspace with plants and wooden tables"></div>

<!-- About -->
<section class="abs about" role="img" aria-label="Dark modern tower facade at dusk">
  <h2>Discover Velmor Spire Nine</h2>
  <p class="about-lead">Lorem ipsum dolor sit amet, consectetur adipiscing elit. Sed do eiusmod tempor incididunt ut labore et dolore magna aliqua. Ut enim ad minim veniam, quis nostrud exercitation ullamco laboris nisi ut aliquip ex ea commodo consequat.</p>
  <div class="pillar" style="left:59px"><h3>Our Vision</h3><p>Lorem ipsum dolor sit amet, consectetur adipiscing elit. Sed do eiusmod tempor incididunt ut labore et dolore magna aliqua.</p></div>
  <div class="pillar" style="left:397px"><h3>Our Mission</h3><p>Lorem ipsum dolor sit amet, consectetur adipiscing elit. Sed do eiusmod tempor incididunt ut labore et dolore magna aliqua.</p></div>
  <div class="pillar" style="left:733px"><h3>Our Values</h3><p>Lorem ipsum dolor sit amet, consectetur adipiscing elit. Sed do eiusmod tempor incididunt ut labore et dolore magna aliqua.</p></div>
</section>

<!-- Contact -->
<section>
  <div class="photo" style="left:0;top:4012px;width:492px;height:490px;background:linear-gradient(180deg,#f7f7f7 0%,#ececec 100%)" role="img" aria-label="Smiling receptionist in a dark suit greeting visitors"></div>
  <div class="abs contact-panel"></div>
  <h2 class="abs" style="left:519px;top:4040px;font-size:30px;font-weight:400;color:#555">Get in Touch</h2>
  <div class="rule" style="left:519px;top:4085px"></div>
  <p class="abs" style="left:519px;top:4096px;font-size:13px;color:#666">Have questions or ready to learn more about Velmor Spire Nine?</p>
  <div class="field" style="left:519px;top:4140px;width:202px;height:32px">Name</div>
  <div class="field" style="left:730px;top:4140px;width:202px;height:32px">Email</div>
  <div class="field" style="left:942px;top:4140px;width:202px;height:32px">Phone Number</div>
  <div class="field" style="left:519px;top:4184px;width:625px;height:245px">Message</div>
  <a class="btn btn-dark" style="left:800px;top:4442px;width:64px;height:34px">Send</a>
</section>

<!-- Footer -->
<footer>
  <div class="abs footer"></div>
  <span class="abs" style="left:120px;top:4617px;width:32px;height:32px;background:#e8d7c6"></span>
  <span class="abs" style="left:53px;top:4688px;width:166px;text-align:center;font-family:'Montserrat',sans-serif;font-size:17px;color:var(--white)">Velmor Spire Nine</span>
  <span class="abs social" style="left:54px;top:4732px"></span>
  <span class="abs social" style="left:98px;top:4732px"></span>
  <span class="abs social" style="left:142px;top:4732px"></span>
  <span class="abs social" style="left:186px;top:4732px"></span>

  <span class="abs f-head" style="left:277px;top:4612px">Contact</span>
  <span class="abs f-text" style="left:277px;top:4656px">Phone</span><span class="abs f-text" style="left:387px;top:4656px">: +1 (XXX) XXX-XXXX</span>
  <span class="abs f-text" style="left:277px;top:4684px">Email</span><span class="abs f-text" style="left:387px;top:4684px">: info@velmorspirenine.com</span>
  <span class="abs f-text" style="left:277px;top:4712px">Address</span><span class="abs f-text" style="left:387px;top:4712px">: Lorem ipsum dolor sit amet, consectetur adipiscing elit</span>
  <span class="abs f-text" style="left:277px;top:4740px">Business Hours : Monday - Friday, 9:00 AM - 5:00 PM</span>

  <span class="abs f-head" style="left:808px;top:4612px">Explore Us</span>
  <span class="abs f-text" style="left:808px;top:4656px">Residences</span>
  <span class="abs f-text" style="left:808px;top:4701px">Office Spaces</span>
  <span class="abs f-text" style="left:808px;top:4746px">About Us</span>

  <span class="abs f-head" style="left:957px;top:4612px">Subscribe to Our Newsletter</span>
  <div class="abs" style="left:957px;top:4655px;width:187px;height:34px;background:var(--white);border-radius:4px;font-size:10px;font-style:italic;color:#888;padding:11px 8px">Enter your email address</div>
  <svg class="abs" style="left:1119px;top:4665px" width="14" height="14" viewBox="0 0 14 14"><path d="M5 3l4 4-4 4" fill="none" stroke="#555" stroke-width="1.4"/></svg>

  <div class="abs" style="left:53px;top:4791px;width:1091px;height:1px;background:rgba(255,255,255,.55)"></div>
  <span class="abs f-text" style="left:0;width:1196px;top:4818px;text-align:center;font-size:11.5px">Copyright © 2024 Velmor Spire Nine. All Rights Reserved.</span>
</footer>

</body>
</html>
```